Redesign Of Current Landing Page

I need to redesign this landing page https://www.brightlanepromo.biz/?page=landing&landing=23 (Please do not opt in because when you do it will show you the home page. Please clear your cookies before going to this url above to view the 1 page landing page.)

Please use my updated website as a reference for colors and logo.
http://sitecradlewerk.com/dh/bpq/index.html

I would like the call to action to be a button that opens into a lead form...

Button would be "Download Samples"

Target Market(s)

small business owners

Industry/Entity Type

Marketing

Number of Pages Required

1 page

Colors

Designer to choose colors to be used in the design.

Requirements
Must have
• must be full responsive on all devices
Nice to have
• must have a legitimate professional apeal to it
Should not have
• open

```html
<!DOCTYPE html>
<html lang="en">
<head>
<meta charset="utf-8">
<title>Brightlane Promo Group – Attract More Customers</title>
<link href="https://fonts.googleapis.com/css2?family=Lato:wght@400;700;900&display=swap" rel="stylesheet">
<style>
:root{
  --blue:#1f64b8;
  --blue-deep:#0d3f86;
  --orange:#f7941d;
  --ink:#222;
  --muted:#444;
  --grey:#ebecee;
  --white:#fff;
  --ring:#3d7bc8;
}
*{box-sizing:border-box;margin:0;padding:0}
html,body{width:1200px;height:4369px;overflow:hidden}
body{font-family:'Lato',sans-serif;color:var(--ink);background:var(--white)}
section{position:relative;width:1200px;overflow:hidden}
.btn{display:block;margin:0 auto;width:445px;height:58px;line-height:58px;background:var(--orange);color:#1a1a1a;font-weight:900;font-size:18px;text-align:center;text-transform:uppercase;text-decoration:none;border-radius:2px}
.section-title{color:var(--blue);font-weight:900;font-size:30px;text-align:center;text-transform:uppercase;line-height:1.25}

/* hero */
.hero{height:664px;background:linear-gradient(180deg,#3a6fa8 0%,#6f8db8 28%,#d79a7e 52%,#b0607a 70%,#5b3f6c 100%)}
.hero-bg{position:absolute;inset:0}
.topbar{position:absolute;left:0;right:0;top:0;height:80px;display:flex;align-items:center;padding:0 130px}
.brand{display:flex;align-items:center;gap:10px;color:var(--white);font-weight:900;font-size:30px;letter-spacing:1px}
.brand-dot{width:36px;height:36px;border-radius:50%;background:var(--blue)}
.contact{margin-left:auto;display:flex;gap:40px;color:var(--white);font-weight:700;font-size:15px}
.contact span{display:flex;align-items:center;gap:8px}
.contact i{width:20px;height:20px;border-radius:50%;background:var(--orange);display:inline-flex;align-items:center;justify-content:center}
.hero-box{position:absolute;left:320px;top:190px;width:555px;height:393px;background:rgba(30,30,35,.72);text-align:center;color:var(--white);padding-top:32px}
.hero-box h1{font-weight:900;font-size:36px;line-height:1.2;text-transform:uppercase}
.hero-box .lead{font-size:24px;line-height:1.25;margin-top:6px}
.hero-box .sub{font-size:16px;line-height:1.4;margin-top:24px}
.hero-box .btn{margin-top:30px;width:465px}

/* feature columns */
.cols{display:flex;justify-content:center}
.col{width:250px;text-align:center}
.ring{width:134px;height:134px;border-radius:50%;border:2px solid var(--ring);margin:0 auto;display:flex;align-items:center;justify-content:center}
.col h3{font-weight:400;font-size:19px;margin-top:28px;line-height:1.2}
.col p{font-size:12.5px;line-height:1.45;margin-top:10px;color:var(--muted);padding:0 22px}

.distribution{height:618px;background:var(--grey);padding-top:68px}
.distribution .cols{margin-top:48px}
.distribution .btn{margin-top:56px}

.offers{height:728px;padding-top:60px}
.offers .cols{margin-top:58px}
.photo{width:163px;height:163px;border-radius:50%;margin:0 auto}
.offers .col h3{margin-top:22px;font-size:18px}
.more{display:block;margin-top:18px;color:var(--blue);font-weight:900;font-size:13px;text-transform:uppercase}
.offers .btn{margin-top:50px}

.imagine{height:597px;background:var(--grey);padding:52px 0 0 131px}
.imagine h2{color:var(--blue);font-weight:900;font-size:30px;text-transform:uppercase}
.imagine-box{margin-top:24px;width:795px;height:298px;border:1px solid #cfd1d4;background:#f2f3f4;padding:26px 330px 0 40px;font-size:15px;line-height:1.45}
.imagine-box p+p{margin-top:18px}
.magnet{position:absolute;left:626px;top:2170px;width:423px;height:292px}
.imagine .btn{margin:44px 0 0}
.imagine .btn{width:446px}

.how{height:472px;background:linear-gradient(180deg,#0f4f9e 0%,#1d6ac0 45%,#2d7cc8 70%,#1e5fa8 100%);padding-top:56px;text-align:center;color:var(--white)}
.how h2{color:var(--orange);font-weight:900;font-size:30px;text-transform:uppercase}
.how p{width:820px;margin:22px auto 0;font-size:15px;line-height:1.45}
.how .btn{margin-top:42px}

.why{height:650px;padding-top:90px}
.why .cols{margin-top:106px}
.why .col{width:162px}
.why .col p{font-size:12px;color:var(--ink);padding:0;margin-top:26px}
.why .btn{margin-top:60px}

.testimonials{height:576px;background:var(--grey);padding-top:66px}
.quote{position:relative;width:560px;margin:44px auto 0;font-size:15px;line-height:1.6;color:var(--muted);text-align:center}
.quote .mark{position:absolute;font-size:64px;font-weight:900;color:#333;line-height:1}
.quote .open{left:-52px;top:-18px}
.quote .close{right:-52px;bottom:-62px}
.author{text-align:center;margin-top:34px;font-size:12px;color:var(--muted)}
.author b{display:block;color:var(--blue)}
.testimonials .btn{margin-top:60px}

.footer{height:64px;background:#dcdde0;text-align:center;line-height:64px;font-size:12px;color:var(--muted)}
.footer .page{position:absolute;right:24px;top:0}
</style>
</head>
<body>

<section class="hero">
  <div class="hero-bg" role="img" aria-label="Airliner flying above sunset clouds"></div>
  <header class="topbar">
    <div class="brand"><span class="brand-dot"></span>BLPG</div>
    <div class="contact">
      <span><i><svg width="11" height="11" viewBox="0 0 24 24"><path fill="#fff" d="M6.6 10.8a15 15 0 006.6 6.6l2.2-2.2c.3-.3.7-.4 1-.2 1.1.4 2.3.6 3.6.6.6 0 1 .4 1 1V20c0 .6-.4 1-1 1A17 17 0 013 4c0-.6.4-1 1-1h3.5c.6 0 1 .4 1 1 0 1.3.2 2.5.6 3.6.1.3 0 .7-.2 1z"/></svg></i>1-800-555-0142</span>
      <span><i><svg width="11" height="11" viewBox="0 0 24 24"><circle cx="12" cy="12" r="9" fill="none" stroke="#fff" stroke-width="3"/><path d="M12 7v5l3 2" stroke="#fff" stroke-width="3" fill="none"/></svg></i>MON-FRI 8AM-5PM PST</span>
    </div>
  </header>
  <div class="hero-box">
    <h1>Attract More<br>Customers</h1>
    <p class="lead">who spend more money with your<br>business more often!</p>
    <p class="sub">Using Free Vacation &amp; Cruise Certificates And Other<br>Incentives Without Breaking The Bank!</p>
    <a class="btn" href="#">Download Free Samples Of Our Incentives</a>
  </div>
</section>

<section class="distribution">
  <h2 class="section-title">Easy Distribution of Incentives</h2>
  <div class="cols">
    <div class="col">
      <div class="ring"><svg width="54" height="54" viewBox="0 0 24 24" fill="none" stroke="#1f64b8" stroke-width="1.6"><rect x="6" y="3" width="12" height="6"/><rect x="3" y="9" width="18" height="8" rx="1"/><rect x="6" y="14" width="12" height="7"/></svg></div>
      <h3>Print</h3>
      <p>Download PDF certificates to print and physically hand them out or mail them to your customers.</p>
    </div>
    <div class="col">
      <div class="ring"><svg width="54" height="54" viewBox="0 0 24 24" fill="#1f64b8"><path d="M2 6h20v12H2z"/><path d="M2 6l10 7 10-7" stroke="#fff" stroke-width="1.4" fill="none"/></svg></div>
      <h3>E-Mail</h3>
      <p>Email E-Certificates to your customers individually or in bulk with just one click</p>
    </div>
    <div class="col">
      <div class="ring"><svg width="54" height="54" viewBox="0 0 24 24"><circle cx="12" cy="12" r="10" fill="#1f64b8"/><path d="M7 6c2 1 3 3 2 5s1 3 2 5M15 4c-1 2 0 4 2 5s2 3 1 5" stroke="#fff" stroke-width="1.4" fill="none"/></svg></div>
      <h3>Online Automation</h3>
      <p>Install our HTML banners on the thank you or check out pages of your website to automate the distribution of our incentives.</p>
    </div>
    <div class="col">
      <div class="ring"><svg width="54" height="54" viewBox="0 0 24 24" fill="#1f64b8"><path d="M3 4h12a2 2 0 012 2v6a2 2 0 01-2 2H8l-4 3v-3H3a2 2 0 01-2-2V6a2 2 0 012-2z"/><path d="M19 9h2a2 2 0 012 2v5a2 2 0 01-2 2h-1v3l-4-3h-5a2 2 0 01-2-2" /></svg></div>
      <h3>Text Messaging</h3>
      <p>Send eno-certificates through text messaging with just one click! (COMING SOON)</p>
    </div>
  </div>
  <a class="btn" href="#">Download Free Samples Of Our Incentives</a>
</section>

<section class="offers">
  <h2 class="section-title">For $99/mth you can giveaway an unlimited<br>amount of all our incentives</h2>
  <div class="cols">
    <div class="col">
      <div class="photo" role="img" aria-label="Airplane on a runway at dusk" style="background:linear-gradient(180deg,#3f78b8,#9ab3cf 55%,#4b4f56)"></div>
      <h3>Vacation Getaway<br>Certificates</h3>
      <p>7 Night Hotel Stays, Cruises &amp; Airfares Up To $3000.00 Retail Value Your Customers Just Pay Taxes!</p>
      <span class="more">More Details</span>
    </div>
    <div class="col">
      <div class="photo" role="img" aria-label="Chef plating a restaurant dish" style="background:radial-gradient(circle at 50% 60%,#d8d4cf,#6a5f58 60%,#2b2826)"></div>
      <h3>Restaurant Gift<br>Certificates</h3>
      <p>$25-$300 Retail Value Thousands Of Restaurants Nationwide!</p>
      <span class="more">More Details</span>
    </div>
    <div class="col">
      <div class="photo" role="img" aria-label="Glowing electronic circuit board" style="background:radial-gradient(circle,#7fb5ff,#1f4f9a 55%,#0b1a33)"></div>
      <h3>Electronic Product<br>Giveaways</h3>
      <p>Tablets, Premium Earbuds, Smart Watches, Mp4 Players $100-$150 Retail Value</p>
      <span class="more">More Details</span>
    </div>
    <div class="col">
      <div class="photo" role="img" aria-label="Fuel nozzle at a gas pump" style="background:linear-gradient(135deg,#e9ece8,#b9c0b6 50%,#2f8a3a)"></div>
      <h3>Gas Or Grocery<br>Rewards</h3>
      <p>Available In $50-$100 Denominations</p>
      <span class="more">More Details</span>
    </div>
  </div>
  <a class="btn" href="#">Download Free Samples Of Our Incentives</a>
</section>

<section class="imagine">
  <h2>Imagine</h2>
  <div class="imagine-box">
    <p>Being able to create exciting give away promotions that will boost your sales without ever having to worry about cost.</p>
    <p>Brightlane Promo Group, Inc. provides high-perceived value promotional incentives to businesses that want to advertise an exciting Give Away that will instantly attract more customers from your existing advertising efforts.</p>
    <p>Your business can give away incentive certificates that are redeemable for luxury hotel &amp; resort stays with airfare included, cruises, cash for gas, groceries, dining and even electronic goods.</p>
  </div>
  <a class="btn" href="#">Download Free Samples Of Our Incentives</a>
</section>
<div class="magnet" role="img" aria-label="Red horseshoe magnet pulling silver balls" style="position:absolute;background:radial-gradient(ellipse at 62% 60%,#c8202a 0%,#c8202a 22%,rgba(200,32,42,0) 42%),radial-gradient(ellipse at 35% 35%,#b9bcc0 0%,rgba(185,188,192,0) 40%)"></div>

<section class="how">
  <div class="hero-bg" role="img" aria-label="Overwater bungalows on a tropical blue lagoon"></div>
  <div style="position:relative">
    <h2>How Can We Do It?</h2>
    <p>We help fill empty rooms for thousands of hotels and resorts in hundreds of destinations around the world as well as the major cruise lines. Hotels and resorts are rarely full so when we place someone in their empty rooms, they end up making it up when travelers spend money on room service, spa services, eat at their in-house restaurants, casino and take advantage of other amenities that drive revenue.</p>
    <p>We also help over 19,000 restaurants, electronic manufacturers, the major gas companies and top grocery chains in the U.S and Canada increase brand awareness as well as increase customer loyalty.</p>
    <a class="btn" href="#">Download Free Samples Of Our Incentives</a>
  </div>
</section>

<section class="why">
  <h2 class="section-title">Why offer incentives<br>to customers?</h2>
  <div class="cols">
    <div class="col">
      <div class="ring"><svg width="56" height="56" viewBox="0 0 24 24" fill="none" stroke="#1f64b8" stroke-width="1.6"><path d="M3 3v18h18"/><path d="M7 17v-5M11 17V9M15 17v-6M19 17V6"/><path d="M6 9l4-3 4 3 6-5"/></svg></div>
      <p>Increase Responses<br>From Your Existing Ads</p>
    </div>
    <div class="col">
      <div class="ring"><svg width="56" height="56" viewBox="0 0 24 24" fill="#1f64b8"><circle cx="8" cy="14" r="5"/><circle cx="8" cy="14" r="2" fill="#fff"/><circle cx="17" cy="7" r="3.5"/><circle cx="17" cy="7" r="1.3" fill="#fff"/><circle cx="18" cy="17" r="2.5"/></svg></div>
      <p>#1 Sales Closing Tool -<br>Gift w/ Purchase</p>
    </div>
    <div class="col">
      <div class="ring"><svg width="56" height="56" viewBox="0 0 24 24" fill="#1f64b8"><circle cx="12" cy="9" r="7"/><circle cx="12" cy="9" r="4" fill="#fff"/><path d="M8 15l-2 8 3-2 2 2 1-7zM16 15l2 8-3-2-2 2-1-7z"/></svg></div>
      <p>Build Brand<br>Awareness and Trust</p>
    </div>
    <div class="col">
      <div class="ring"><svg width="56" height="56" viewBox="0 0 24 24" fill="#1f64b8"><rect x="9" y="3" width="6" height="6" rx="1"/><path d="M2 12l5 4h10l5-4v3l-5 5H7l-5-5z"/></svg></div>
      <p>Insure The Sale Over<br>Your Competition</p>
    </div>
    <div class="col">
      <div class="ring"><svg width="56" height="56" viewBox="0 0 24 24" fill="#1f64b8"><path d="M1 9l5-3 5 3 3-2 5 2 4 2-3 5-6 3-4-3-6-2z"/><path d="M8 12l4 3M10 10l4 3" stroke="#fff" stroke-width="1"/></svg></div>
      <p>Boost Repeat and<br>Referral Business</p>
    </div>
    <div class="col">
      <div class="ring"><svg width="56" height="56" viewBox="0 0 24 24" fill="none" stroke="#1f64b8" stroke-width="1.6"><path d="M5 7a8 8 0 0113-1M19 17a8 8 0 01-13 1"/><path d="M18 2v4h-4M6 22v-4h4"/><text x="12" y="15.5" font-size="9" font-family="Lato,sans-serif" font-weight="900" text-anchor="middle" fill="#1f64b8" stroke="none">$</text></svg></div>
      <p>Improve<br>Retention Rates</p>
    </div>
  </div>
  <a class="btn" href="#">Download Free Samples Of Our Incentives</a>
</section>

<section class="testimonials">
  <h2 class="section-title">Testimonials</h2>
  <div class="quote">
    <span class="mark open">&ldquo;</span>
    I began using your incentives two years ago to boost lead generation efforts. I have experienced a 63% increase in lead captures. And, even more importantly, my sales have increased as well. The ability to offer unlimited certificates and not having to pay for each certificate I give away is perhaps the best feature of the program, but having the flexibility to email or print certificates for my customers is also wonderful. I even use your html banners to automate my promotions right on my website!
    <span class="mark close">&rdquo;</span>
  </div>
  <div class="author"><b>Dana R.</b>Oakridge, TN</div>
  <a class="btn" href="#">Download Free Samples Of Our Incentives</a>
</section>

<footer class="footer">
  &copy; 2017 &nbsp;Brightlane Promo Group, Inc. - All Rights Reserved
  <span class="page">9/27</span>
</footer>

</body>
</html>
```